Brisk Fixwell business card

I need business card for my business, I think you have all my details.six months ago I design with you car wrap design. We would like to design both side of the card. On front of card we would like logo , Name and our contact details.
At the back we are looking to mentioned our services.
The name will be:
Faridoullan Mestor
Managing Director
Ph:07952338417
Email:info@brisk-fixwell.com
Web:www.brisk-fixwell.com
So we have our logo, you don’t need to change the logo.
Please see the attachment.
Thanks

Target Market(s)

Home improvement

Industry/Entity Type

Home Improvement

Contact Information for Business Card

Company name: Brisk Fixwell
Name: Faridoullan Mestor
Position: Director
Ph:07952338417
Web: www.brisk-fixwell.com
Add: 42 Corvale Road
Hounslow
TW3 9KD
SECOND PERSON
Nizamuddel mestor
Position: Handyman
Ph: 07812 564037
Email: info@brisk-fixwell.com
Add: 18 Brackwin Lane Road
Hounslow
TW6 2LB

```html
<!DOCTYPE html>
<html lang="en">
<head>
<meta charset="utf-8">
<title>Brisk Fixwell – Business Card</title>
<link href="https://fonts.googleapis.com/css2?family=Roboto:wght@400;500&family=Saira+Semi+Condensed:wght@600;700&display=swap" rel="stylesheet">
<style>
  :root {
    --navy: #222561;
    --red: #b81f1d;
    --grey: #8a8a8a;
    --paper: #f4f4f4;
    --backdrop: #b5b5b5;
    --white: #ffffff;
    --faint: #3b3f80;
    --ink: #333333;
  }
  * { margin: 0; padding: 0; box-sizing: border-box; }
  html, body { width: 1200px; height: 576px; overflow: hidden; }
  body { background: var(--backdrop); position: relative; font-family: "Roboto", sans-serif; }

  .card { position: absolute; border-radius: 10px; overflow: hidden; }

  /* Back side: services */
  .card-back { left: 82px; top: 139px; width: 485px; height: 293px; background: var(--navy); }
  .card-back .brand-emboss {
    position: absolute; left: 0; right: 0; top: 62px;
    display: flex; flex-direction: column; align-items: center; gap: 14px;
  }
  .card-back .brand-emboss-square { width: 46px; height: 46px; background: var(--faint); }
  .card-back .brand-emboss-name {
    font-family: "Saira Semi Condensed", sans-serif; font-weight: 700; font-size: 56px;
    color: var(--faint); line-height: 1; letter-spacing: 0.5px;
  }
  .card-back .services {
    position: absolute; left: 0; right: 0; bottom: 0; height: 47px;
    background: var(--red); color: var(--white);
    display: flex; flex-direction: column; justify-content: center; align-items: center;
    font-size: 13.5px; line-height: 16px;
  }

  /* Front side: name and contacts */
  .card-front { left: 602px; top: 138px; width: 480px; height: 291px; background: var(--paper); }
  .card-front .waves { position: absolute; inset: 0; }
  .card-front .brand {
    position: absolute; left: 50px; top: 36px;
    display: flex; flex-direction: column; align-items: flex-start; gap: 12px;
  }
  .card-front .brand-square { width: 56px; height: 56px; background: var(--red); margin-left: 56px; }
  .card-front .brand-name {
    font-family: "Saira Semi Condensed", sans-serif; font-weight: 700; font-size: 50px;
    color: var(--navy); line-height: 1;
  }
  .card-front .person { position: absolute; right: 25px; top: 54px; text-align: right; }
  .card-front .person-name {
    font-family: "Saira Semi Condensed", sans-serif; font-weight: 700; font-size: 20px;
    color: var(--navy); line-height: 24px;
  }
  .card-front .person-title { font-size: 12.5px; color: var(--ink); margin-right: 10px; margin-top: 1px; }
  .card-front .contacts {
    position: absolute; right: 18px; top: 211px; list-style: none; color: var(--white);
    font-size: 13px;
  }
  .card-front .contacts li {
    display: flex; justify-content: flex-end; align-items: center; gap: 10px; height: 18px;
  }
  .card-front .contacts svg { width: 11px; height: 11px; fill: var(--white); }
</style>
</head>
<body>

<section class="card card-back">
  <div class="brand-emboss">
    <span class="brand-emboss-square"></span>
    <span class="brand-emboss-name">Brisk Fixwell</span>
  </div>
  <div class="services">
    <span>Electrical &nbsp;|&nbsp; Carpentry &nbsp;|&nbsp; Plumbing &nbsp;|&nbsp; Plastering &nbsp;|&nbsp; Flooring</span>
    <span>Fencing &nbsp;|&nbsp; Decking &nbsp;|&nbsp; Painting &amp; Decorating</span>
  </div>
</section>

<section class="card card-front">
  <svg class="waves" viewBox="0 0 480 291" preserveAspectRatio="none">
    <path d="M0,222 C60,240 140,262 240,250 C180,262 90,262 0,248 Z" fill="var(--grey)"/>
    <path d="M0,246 C80,290 200,285 290,228 C360,185 420,175 480,172 L480,291 L0,291 Z" fill="var(--navy)"/>
    <path d="M38,232 C120,255 210,250 280,212 C350,175 410,160 480,158 L480,167 C410,170 355,184 290,220 C215,258 120,260 38,232 Z" fill="var(--red)"/>
  </svg>

  <div class="brand">
    <span class="brand-square"></span>
    <span class="brand-name">Brisk Fixwell</span>
  </div>

  <div class="person">
    <div class="person-name">Faridoullan Mestor</div>
    <div class="person-title">Managing Director</div>
  </div>

  <ul class="contacts">
    <li>07952338417
      <svg viewBox="0 0 16 16"><path d="M2 6c0-3 12-3 12 0v1h-3V5.5H5V7H2zM4 8h8l2 5H2z"/></svg>
    </li>
    <li>brisk-fixwell.com
      <svg viewBox="0 0 16 16"><path d="M1 3h14v10H1zM2 4.5v.5l6 4 6-4v-.5l-6 4z" fill-rule="evenodd"/></svg>
    </li>
    <li>info@brisk-fixwell.com
      <svg viewBox="0 0 16 16"><path d="M8 1a7 7 0 1 0 0 14A7 7 0 0 0 8 1zm0 1.5c.9 0 1.9 2 2.1 4.7H5.9C6.1 4.5 7.1 2.5 8 2.5zM2.6 8.8h1.9c.1 1.7.5 3.2 1.1 4.2a5.5 5.5 0 0 1-3-4.2zm0-1.6a5.5 5.5 0 0 1 3-4.2c-.6 1-1 2.5-1.1 4.2zm3.3 1.6h4.2c-.2 2.7-1.2 4.7-2.1 4.7s-1.9-2-2.1-4.7zm5.6 0h1.9a5.5 5.5 0 0 1-3 4.2c.6-1 1-2.5 1.1-4.2zm0-1.6c-.1-1.7-.5-3.2-1.1-4.2a5.5 5.5 0 0 1 3 4.2z"/></svg>
    </li>
  </ul>
</section>

</body>
</html>
```